Harbor Crestline (Business Card Design)

Need business cards designed. Something modern, chic, and sleek. Mabye the back of the card should be the navy blue that is in the logo and then just the logo on the back.

Target Market(s)

Those in the hotel, office, and renovation industry

Contact Information for Business Card

1. Logo 2. Dorian Fenwick 3. CEO/Founder 4. Phone: (833) HarbCre / (833) 427-2731 5. Email: dorian@theharborcrestline.com 6. Website: www.theharborcrestline.com

Font styles to use
Other font styles liked:
• Look at the logo font and base the font for everything else off of that.

Colors
0054AA
0677BA
7BADD7
CADEEF
E8F1F8

Requirements
Must have
• Colors that are associated in the logo
Nice to have
• Sleek modern clean and chic design.

```html
<!DOCTYPE html>
<html lang="en">
<head>
<meta charset="utf-8">
<title>Harbor Crestline – Business Card</title>
<link rel="stylesheet" href="https://fonts.googleapis.com/css2?family=Montserrat:wght@600&family=Poppins:wght@400;600&display=swap">
<style>
  :root {
    --bg: #e9ebef;
    --navy: #0b1a44;
    --navy-deep: #07123a;
    --navy-bright: #14309a;
    --gold: #d3a94c;
    --white: #ffffff;
    --rule: #6f7a9c;
  }
  * { box-sizing: border-box; margin: 0; padding: 0; }
  html, body { width: 1200px; height: 1108px; overflow: hidden; }
  body {
    background: var(--bg);
    font-family: "Poppins", sans-serif;
    position: relative;
  }
  .card {
    position: absolute;
    top: 234px;
    width: 400px;
    height: 640px;
    border-radius: 22px;
    overflow: hidden;
    box-shadow: 0 14px 30px rgba(0,0,0,.22);
  }
  .card--front { left: 160px; background: var(--navy); color: var(--white); }
  .card--back { left: 640px; background: var(--navy-deep); }

  .brand {
    position: absolute;
    top: 150px;
    left: 0; right: 0;
    display: flex;
    flex-direction: column;
    align-items: center;
    gap: 22px;
  }
  .brand__square { width: 14px; height: 14px; background: var(--gold); }
  .brand__name {
    font-family: "Montserrat", sans-serif;
    font-weight: 600;
    font-size: 30px;
    letter-spacing: 4px;
    text-transform: uppercase;
    color: var(--white);
    text-align: center;
    line-height: 1.25;
  }

  .person {
    position: absolute;
    top: 372px;
    left: 0; right: 0;
    text-align: center;
  }
  .person__name { font-weight: 600; font-size: 24px; letter-spacing: .5px; text-transform: uppercase; }
  .person__title { font-size: 15px; color: var(--gold); text-transform: uppercase; margin-top: 2px; }

  .divider {
    position: absolute;
    top: 452px;
    left: 40px; right: 40px;
    display: flex;
    align-items: center;
    gap: 10px;
  }
  .divider__line { flex: 1; height: 1px; background: var(--rule); }
  .divider__icons { display: flex; gap: 7px; }
  .icon {
    width: 26px; height: 26px;
    border-radius: 4px;
    background: var(--gold);
    display: flex; align-items: center; justify-content: center;
  }
  .icon svg { width: 16px; height: 16px; }

  .contact {
    position: absolute;
    top: 494px;
    left: 0; right: 0;
    text-align: center;
    font-size: 15.5px;
    line-height: 1.6;
  }

  .back-pattern {
    position: absolute;
    inset: 0;
    background:
      linear-gradient(135deg, rgba(20,48,154,.55) 0%, rgba(20,48,154,.15) 45%, rgba(7,18,58,0) 70%),
      linear-gradient(180deg, var(--navy-deep), var(--navy));
  }
  .back-brand {
    position: absolute;
    top: 440px;
    left: 0; right: 0;
    display: flex;
    justify-content: center;
    align-items: center;
    gap: 10px;
  }
  .back-brand__square { width: 10px; height: 10px; background: var(--gold); }
  .back-brand__name {
    font-family: "Montserrat", sans-serif;
    font-weight: 600;
    font-size: 15px;
    letter-spacing: 2px;
    text-transform: uppercase;
    color: var(--white);
  }
</style>
</head>
<body>
  <section class="card card--front">
    <div class="brand">
      <span class="brand__square"></span>
      <div class="brand__name">Harbor<br>Crestline</div>
    </div>

    <div class="person">
      <div class="person__name">Dorian Fenwick</div>
      <div class="person__title">CEO/Founder</div>
    </div>

    <div class="divider">
      <span class="divider__line"></span>
      <div class="divider__icons">
        <span class="icon" aria-label="Phone">
          <svg viewBox="0 0 16 16"><path d="M4 2l2 3-1.3 1.3a8 8 0 0 0 5 5L11 10l3 2-1 2.5C7 14 2 9 1.5 3z" fill="#fff"/></svg>
        </span>
        <span class="icon" aria-label="Email">
          <svg viewBox="0 0 16 16"><rect x="1.5" y="3.5" width="13" height="9" fill="none" stroke="#fff" stroke-width="1.4"/><path d="M1.5 3.5L8 9l6.5-5.5" fill="none" stroke="#fff" stroke-width="1.4"/></svg>
        </span>
        <span class="icon" aria-label="Website">
          <svg viewBox="0 0 16 16"><circle cx="8" cy="8" r="6" fill="none" stroke="#fff" stroke-width="1.4"/><path d="M2 8h12M8 2c-3 3-3 9 0 12M8 2c3 3 3 9 0 12" fill="none" stroke="#fff" stroke-width="1.1"/></svg>
        </span>
      </div>
      <span class="divider__line"></span>
    </div>

    <div class="contact">
      <p>(833) HarbCre / (833) 427-2731</p>
      <p>dorian@theharborcrestline.com</p>
      <p>www.theharborcrestline.com</p>
    </div>
  </section>

  <section class="card card--back">
    <div class="back-pattern" role="img" aria-label="Repeating embossed brand pattern in deep and bright navy"></div>
    <div class="back-brand">
      <span class="back-brand__square"></span>
      <span class="back-brand__name">Harbor Crestline</span>
    </div>
  </section>
</body>
</html>
```